Website design for legal tech start up in Switzerland (B2B)

We are for a legal tech start up in Switzerland called KOVA. We have been running since August 2016. This will be our first live website.

We need a website designed and business card design for our start-up in Switzerland. We also need the Web design to be converted into HTML and CSS files.

Function of website:
• To inform potential customers of our services
• Form a key part of our digital marketing and sales footprint.
• Branding

Please find attached logo.
Updates

Project Deadline Extended Reason: Giving us time to review submissions and provide opportunity for more submissions. Added Thursday, February 16, 2017

Project Deadline Extended
Reason: Looking for more idea's not necessarily set on blue and grey colours only.

Target Market(s)

B2B tech powered legal services.

Industry/Entity Type

Legal

Contact Information for Business Card

Lean and slick design.

Coding

Coded - Design and coding required

Number of Pages Required

5+ page

Requirements
Must have
• VERY LEAN AND CLEAN DESIGN!
• We have received many great standard designs, but we are looking for something more out-of-the box: You can get inspiration from these designs: http://www.pixelvane.com/websites/clean/
• Thanks!!
• Easy content management system
• Well structured coding for additional development
• Responsive webpage for all types of devices
• SEO optimized
• Tabs (Home, services, team, careers, blog, contact us)
• Colour scheme complementary to logo
Nice to have
• Look and Design - Approachable, High-tech, Modern
• Easy to add chat bot capability in future
Should not have
• Too busy/ too much clutter
• Not take to long to load

```html
<!DOCTYPE html>
<html lang="en">
<head>
<meta charset="utf-8">
<title>KOVA – Legal Startup Company</title>
<link href="https://fonts.googleapis.com/css2?family=Lato:ital,wght@0,400;0,700;0,900;1,400&display=swap" rel="stylesheet">
<style>
:root{
  --navy:#1b3a6b;
  --navy-deep:#16335f;
  --ink:#333a45;
  --muted:#7b8089;
  --rule:#d9dce1;
  --band:#eef1f6;
  --white:#ffffff;
}
*{box-sizing:border-box;margin:0;padding:0}
html,body{width:1200px;height:2727px;overflow:hidden}
body{position:relative;background:var(--white);font-family:"Lato",Arial,sans-serif;color:var(--ink)}
.abs{position:absolute}
/* header */
.site-header{left:0;top:0;width:1200px;height:91px}
.brand{left:98px;top:20px;font-size:42px;font-weight:900;letter-spacing:2px;color:var(--navy)}
.top-contacts{right:98px;top:13px;display:flex;gap:26px;font-size:16px;font-weight:700;color:var(--ink)}
.top-contacts span{display:flex;align-items:center;gap:12px}
.ring{width:30px;height:30px;border:1.5px solid var(--rule);border-radius:50%;display:flex;align-items:center;justify-content:center}
.main-nav{right:98px;top:58px;display:flex;gap:26px;font-size:15px;font-weight:700;text-transform:uppercase;color:var(--ink)}
.main-nav .active{color:var(--navy);border-bottom:2px solid var(--navy);padding-bottom:4px}
/* hero */
.hero{left:0;top:91px;width:1200px;height:469px;overflow:hidden}
.hero-photo{position:absolute;inset:0;background:linear-gradient(160deg,#8c7e72 0%,#a9825e 35%,#c59a63 55%,#7d6b58 80%,#5c5a5c 100%)}
.hero-leaves{position:absolute;right:0;top:0;width:260px;height:330px;background:radial-gradient(circle at 80% 20%,#e09a2a 0%,#d07f1c 40%,rgba(208,127,28,0) 72%)}
.hero-overlay{position:absolute;inset:0}
.hero-title{left:98px;top:155px;font-size:40px;font-weight:900;color:var(--white);text-transform:uppercase}
.hero-sub{left:98px;top:210px;width:520px;font-size:21px;font-weight:700;line-height:30px;color:var(--white)}
.hero-btn{left:98px;top:300px;width:189px;height:40px;border:2px solid var(--white);border-radius:22px;background:var(--navy);color:var(--white);font-size:14px;font-weight:900;display:flex;align-items:center;justify-content:center;text-transform:uppercase}
.hero-dots{left:98px;top:406px;display:flex;gap:5px}
.hero-dots i{width:14px;height:14px;border:2px solid var(--white);border-radius:50%}
.hero-dots i.on{background:var(--white)}
/* welcome */
.section-title{font-size:32px;font-weight:900;color:var(--ink);text-transform:uppercase}
.welcome-title{left:0;width:1200px;top:618px;text-align:center}
.welcome-intro{left:200px;width:800px;top:678px;text-align:center;font-size:13px;line-height:24px;color:var(--muted)}
.feature{top:760px;width:260px;text-align:center}
.feature .badge{width:142px;height:142px;margin:0 auto;border:1.5px solid #9aa0a8;border-radius:50%;display:flex;align-items:center;justify-content:center}
.feature h3{margin-top:28px;font-size:18px;font-weight:700;color:var(--ink)}
.feature p{margin-top:12px;font-size:13px;line-height:23px;color:var(--muted)}
.feature .more{display:block;margin-top:15px;font-size:13px;font-weight:900;color:var(--navy)}
/* what we do */
.what-band{left:0;top:1093px;width:1200px;height:400px;background:var(--band)}
.what-title{left:98px;top:1140px}
.what-text{left:98px;top:1198px;width:460px;font-size:13px;line-height:25px;color:var(--muted)}
.what-text p+p{margin-top:20px}
.pill{height:35px;padding:0 20px;border:1.5px solid #8d939b;border-radius:18px;font-size:12px;font-weight:900;color:var(--navy);display:inline-flex;align-items:center;text-transform:uppercase;background:transparent}
.what-btn{left:98px;top:1397px}
.video{left:607px;top:1149px;width:491px;height:285px;border:4px solid var(--white);box-shadow:0 0 0 1px var(--rule);background:linear-gradient(135deg,#3d4652 0%,#c9c8c4 35%,#e8e4dc 60%,#8c8a86 100%)}
.play{position:absolute;left:50%;top:50%;width:60px;height:60px;margin:-30px 0 0 -30px}
/* columns */
.col{top:1548px;width:315px}
.col h2{font-size:26px;font-weight:900;text-transform:uppercase;color:var(--ink);padding-bottom:12px;border-bottom:4px solid var(--ink)}
.col.accent h2{border-bottom-color:var(--navy)}
.col .thumb{margin-top:23px;height:182px;border:3px solid var(--white);box-shadow:0 0 0 1px var(--rule)}
.col p{margin-top:24px;font-size:13px;line-height:23px;color:var(--muted)}
.col .pill{margin-top:26px}
/* testimonial */
.quote-band{left:0;top:2016px;width:1200px;height:209px;background:var(--navy-deep)}
.avatar{left:109px;top:2058px;width:124px;height:124px;border:4px solid var(--white);border-radius:50%;background:radial-gradient(circle at 50% 40%,#c9b6a2 0%,#8d8279 60%,#5a6170 100%)}
.quote-rule{left:270px;top:2058px;width:1px;height:126px;background:rgba(255,255,255,.45)}
.quote-text{left:303px;top:2058px;width:790px;font-size:15px;font-style:italic;line-height:25px;color:var(--white)}
.quote-name{left:307px;top:2157px;font-size:19px;font-weight:700;color:var(--white)}
.arrow{top:2107px}
/* contact */
.contact-title{left:0;width:1200px;top:2287px;text-align:center}
.form-title{left:98px;top:2362px;font-size:20px;font-weight:700}
.field{border:1px solid #c9ccd1;font-size:12px;color:var(--muted);padding:10px 12px;background:var(--white)}
.submit{left:625px;top:2578px;width:79px;height:31px;border:1.5px solid #8d939b;border-radius:16px;font-size:12px;font-weight:900;display:flex;align-items:center;justify-content:center}
.info-title{left:782px;top:2362px;font-size:20px;font-weight:700}
.info-row{left:782px;display:flex;align-items:center;gap:20px;font-size:13px;line-height:24px;color:var(--muted)}
.info-row .ring{width:34px;height:34px}
.socials{left:782px;top:2576px;display:flex;gap:5px}
.socials i{width:30px;height:30px;border-radius:50%;background:var(--navy)}
.footer-rule{left:98px;top:2651px;width:1004px;height:1px;background:var(--rule)}
.copyright{left:0;width:1200px;top:2678px;text-align:center;font-size:13px;color:var(--muted)}
</style>
</head>
<body>

<header class="site-header abs">
  <div class="brand abs">KOVA</div>
  <div class="top-contacts abs">
    <span><i class="ring"><svg width="14" height="14" viewBox="0 0 24 24"><path fill="#333a45" d="M6.6 10.8a15 15 0 0 0 6.6 6.6l2.2-2.2c.3-.3.7-.4 1-.2 1.1.4 2.3.6 3.6.6.6 0 1 .4 1 1V20c0 .6-.4 1-1 1A17 17 0 0 1 3 4c0-.6.4-1 1-1h3.5c.6 0 1 .4 1 1 0 1.3.2 2.5.6 3.6.1.3 0 .7-.2 1z"/></svg></i>1 555 014 2290</span>
    <span><i class="ring"><svg width="14" height="14" viewBox="0 0 24 24"><path fill="#333a45" d="M2 5h20v14H2z"/><path d="M2 5l10 8 10-8" stroke="#fff" stroke-width="2" fill="none"/></svg></i>info@kova.ch</span>
  </div>
  <nav class="main-nav abs">
    <span class="active">Home</span><span>Services</span><span>Team</span><span>Careers</span><span>Blog</span><span>Contact Us</span>
    <svg width="14" height="14" viewBox="0 0 24 24"><circle cx="10" cy="10" r="7" stroke="#333a45" stroke-width="3" fill="none"/><path d="M15 15l7 7" stroke="#333a45" stroke-width="3"/></svg>
  </nav>
</header>

<section class="hero abs">
  <div class="hero-photo" role="img" aria-label="Aerial view of a Swiss old town with river and autumn leaves"></div>
  <div class="hero-leaves"></div>
  <svg class="hero-overlay" width="1200" height="469" viewBox="0 0 1200 469">
    <polygon points="0,0 552,0 700,236 552,469 0,469" fill="#1e2f4d" fill-opacity=".55"/>
    <polygon points="552,0 572,0 720,236 572,469 552,469 700,236" fill="#1b3a8b"/>
  </svg>
  <div class="hero-title abs" style="top:155px">Legal Startup Company</div>
  <div class="hero-sub abs">At vero eos et accusamus et iusto odio dignissimos mus qui blan ditiis praesentium volu</div>
  <div class="hero-btn abs">Get More Info</div>
  <div class="hero-dots abs"><i class="on"></i><i></i><i></i><i></i></div>
</section>

<h1 class="section-title welcome-title abs">Welcome to KOVA</h1>
<p class="welcome-intro abs">At vero eos et accusamus et iusto odio dignissimos ducimus qui blanditiis praesentium voluptatum deleniti atque corrupti quos dolores et quas molestias excepturi sint occaecati cupiditate milique sunt in culpa qui officia deserunt mollitia animi, id est</p>

<div class="feature abs" style="left:81px">
  <div class="badge"><svg width="64" height="64" viewBox="0 0 64 64"><path d="M28 6l20 7v16c0 14-9 24-20 29C17 53 8 43 8 29V13z" fill="#1b3a6b"/><path d="M28 12l14 5v12c0 10-6 18-14 22z" fill="#fff" opacity=".25"/><circle cx="46" cy="40" r="13" fill="#fff"/><circle cx="46" cy="40" r="10" fill="#1b3a6b"/><path d="M41 40l4 4 7-7" stroke="#fff" stroke-width="3" fill="none"/></svg></div>
  <h3>Confidential</h3>
  <p>Nam libero tempore, cum soluta no bis est eligendi optio cumque nihili</p>
  <span class="more">READ MORE &gt;&gt;</span>
</div>
<div class="feature abs" style="left:339px">
  <div class="badge"><svg width="64" height="64" viewBox="0 0 64 64"><rect x="6" y="10" width="52" height="46" rx="3" fill="none" stroke="#1b3a6b" stroke-width="3"/><rect x="6" y="10" width="52" height="10" fill="#1b3a6b"/><g fill="#1b3a6b"><rect x="14" y="26" width="6" height="5"/><rect x="24" y="26" width="6" height="5"/><rect x="34" y="26" width="6" height="5"/><rect x="44" y="26" width="6" height="5"/><rect x="24" y="36" width="6" height="5"/><rect x="34" y="36" width="6" height="5"/><rect x="44" y="36" width="6" height="5"/><rect x="34" y="46" width="6" height="5"/><rect x="44" y="46" width="6" height="5"/></g><circle cx="18" cy="48" r="10" fill="#fff" stroke="#1b3a6b" stroke-width="3"/><path d="M18 43v5h4" stroke="#1b3a6b" stroke-width="2.5" fill="none"/></svg></div>
  <h3>Development &amp; Planning</h3>
  <p>Nam libero tempore, cum soluta no bis est eligendi optio cumque nihili</p>
  <span class="more">READ MORE &gt;&gt;</span>
</div>
<div class="feature abs" style="left:603px">
  <div class="badge"><svg width="64" height="64" viewBox="0 0 64 64"><rect x="4" y="14" width="56" height="40" rx="3" fill="#1b3a6b"/><rect x="26" y="8" width="12" height="10" rx="2" fill="#fff" stroke="#1b3a6b" stroke-width="3"/><rect x="10" y="26" width="18" height="20" fill="#fff"/><circle cx="19" cy="33" r="4" fill="#1b3a6b"/><path d="M12 45c0-6 14-6 14 0z" fill="#1b3a6b"/><g fill="#fff"><rect x="34" y="28" width="20" height="3"/><rect x="34" y="35" width="20" height="3"/><rect x="34" y="42" width="14" height="3"/></g></svg></div>
  <h3>Corporate &amp; Insolvency</h3>
  <p>Nam libero tempore, cum soluta no bis est eligendi optio cumque nihili</p>
  <span class="more">READ MORE &gt;&gt;</span>
</div>
<div class="feature abs" style="left:859px">
  <div class="badge"><svg width="64" height="64" viewBox="0 0 64 64"><rect x="16" y="6" width="38" height="48" fill="#fff" stroke="#1b3a6b" stroke-width="3"/><rect x="10" y="12" width="38" height="48" fill="#1b3a6b"/><g fill="#fff"><rect x="16" y="20" width="14" height="3"/><rect x="16" y="27" width="14" height="3"/><rect x="16" y="34" width="14" height="3"/><rect x="16" y="41" width="26" height="3"/><rect x="16" y="48" width="26" height="3"/></g><text x="38" y="36" font-family="Lato,Arial,sans-serif" font-weight="900" font-size="16" fill="#fff" text-anchor="middle">$</text></svg></div>
  <h3>Commercial Litigation</h3>
  <p>Nam libero tempore, cum soluta no bis est eligendi optio cumque nihili</p>
  <span class="more">READ MORE &gt;&gt;</span>
</div>

<section class="what-band abs"></section>
<h2 class="section-title what-title abs">What We Do</h2>
<div class="what-text abs">
  <p>At vero eos et accusamus et iusto odio dignissimos ducimus qui blanditiis prasent ium voluptatum deleniti atque corrupti quo.</p>
  <p>Dolores et quas molestias excepturi sint occaecati cupiditate non provident similiq ue sunt in culpa qui officia deserunt mollitia animi, id est laborum et dolorum fug t harum quidem rerum facilis est et expedita voluptas assumenda est, omnis dolorr epellend poribus autem quibusdam et aut officiis.</p>
</div>
<span class="pill what-btn abs">Read More &gt;&gt;</span>
<div class="video abs" role="img" aria-label="Video still of hands signing a contract at a desk">
  <svg class="play" viewBox="0 0 60 60"><circle cx="30" cy="30" r="30" fill="#1f1f1f" fill-opacity=".85"/><path d="M24 18l18 12-18 12z" fill="#fff"/></svg>
</div>

<div class="col abs" style="left:98px">
  <h2>Expertise</h2>
  <div class="thumb" role="img" aria-label="Hands typing on a laptop keyboard" style="background:linear-gradient(135deg,#e6e7e9 0%,#9ea3aa 45%,#3f444b 100%)"></div>
  <p>Nam libero tempore, cum soluta nobis est eligen optioc umque nihil impedit quo minus id quod maxime placat facere possimus omnis volupta.</p>
  <span class="pill">Read More &gt;&gt;</span>
</div>
<div class="col abs accent" style="left:442px">
  <h2>Careers</h2>
  <div class="thumb" role="img" aria-label="Businessman with coffee reading a tablet" style="background:linear-gradient(120deg,#4e4a3c 0%,#8a6f45 40%,#c0a57a 60%,#2c3a52 100%)"></div>
  <p>Nam libero tempore, cum soluta nobis est eligen optioc umque nihil impedit quo minus id quod maxime placat facere possimus omnis volupta.</p>
  <span class="pill">Read More &gt;&gt;</span>
</div>
<div class="col abs" style="left:787px">
  <h2>Newsroom</h2>
  <div class="thumb" role="img" aria-label="Team meeting silhouetted against a bright office window" style="background:linear-gradient(180deg,#6fb3c6 0%,#d9cfa8 55%,#8a6a40 80%,#3b3026 100%)"></div>
  <p>Nam libero tempore, cum soluta nobis est eligen optioc umque nihil impedit quo minus id quod maxime placat facere possimus omnis volupta.</p>
  <span class="pill">Read More &gt;&gt;</span>
</div>

<section class="quote-band abs"></section>
<svg class="arrow abs" style="left:32px" width="20" height="30" viewBox="0 0 20 30"><path d="M16 3L4 15l12 12" stroke="#9fb0cc" stroke-width="3" fill="none"/></svg>
<svg class="arrow abs" style="left:1148px" width="20" height="30" viewBox="0 0 20 30"><path d="M4 3l12 12L4 27" stroke="#9fb0cc" stroke-width="3" fill="none"/></svg>
<div class="avatar abs" role="img" aria-label="Portrait of a smiling client"></div>
<div class="quote-rule abs"></div>
<blockquote class="quote-text abs">Nam libero tempore, cum soluta nobis est eligendi optio cumque nihil impedit quo minus id quod maxime placeat facere possimus, omnis voluptas assumenda est, omnis dolor repellendus. Temporibus autem quibusdam et aut officiis debitis aut rerum necessitatibus saepe eveniet ut et voluptates repudiandae sint et molestiae</blockquote>
<div class="quote-name abs">- Mathis Ferrand</div>

<h2 class="section-title contact-title abs">Contact Us</h2>
<div class="form-title abs">Get In Touch:</div>
<div class="field abs" style="left:98px;top:2407px;width:297px;height:33px">Name :</div>
<div class="field abs" style="left:407px;top:2407px;width:297px;height:33px">Phone :</div>
<div class="field abs" style="left:98px;top:2451px;width:606px;height:33px">Email :</div>
<div class="field abs" style="left:98px;top:2494px;width:606px;height:71px">Message :</div>
<div class="submit abs">SUBMIT</div>

<div class="info-title abs">Contact Information</div>
<div class="info-row abs" style="top:2405px">
  <i class="ring"><svg width="14" height="16" viewBox="0 0 24 28"><path d="M12 2a9 9 0 0 0-9 9c0 7 9 15 9 15s9-8 9-15a9 9 0 0 0-9-9z" fill="#333a45"/><circle cx="12" cy="11" r="3.5" fill="#fff"/></svg></i>
  <span>145 Lindenweg, 4th Floor<br>Switzerland 8001</span>
</div>
<div class="info-row abs" style="top:2467px">
  <i class="ring"><svg width="14" height="14" viewBox="0 0 24 24"><path fill="#333a45" d="M6.6 10.8a15 15 0 0 0 6.6 6.6l2.2-2.2c.3-.3.7-.4 1-.2 1.1.4 2.3.6 3.6.6.6 0 1 .4 1 1V20c0 .6-.4 1-1 1A17 17 0 0 1 3 4c0-.6.4-1 1-1h3.5c.6 0 1 .4 1 1 0 1.3.2 2.5.6 3.6.1.3 0 .7-.2 1z"/></svg></i>
  <span>1 555 014 2290</span>
</div>
<div class="info-row abs" style="top:2521px">
  <i class="ring"><svg width="14" height="14" viewBox="0 0 24 24"><path fill="#333a45" d="M2 5h20v14H2z"/><path d="M2 5l10 8 10-8" stroke="#fff" stroke-width="2" fill="none"/></svg></i>
  <span>info@kova.ch</span>
</div>
<div class="socials abs" aria-label="Social links"><i></i><i></i><i></i><i></i></div>

<div class="footer-rule abs"></div>
<footer class="copyright abs">Copyrights © 2017, Kova. All Rights Reserved.</footer>

</body>
</html>
```